Design a Website in Wordpress for an Australian Health Training Company in Health related courses

We require a WORDPRESS based Website (due to add on's we need to use for third party software) to replace our old site.
We offer national face to face delivery in medical reception, terminology and also administration.
The website will have around 6 pages and the ability to describe our main 6 courses (perhaps on the Courses page this may be tabs opening up to details for example?)
I have attached a previous sample of a Joomla site which was being developed (please do not feel you have to copy this - but I am just giving it as a sample - copying would be boring). But it gives an idea of look/feel and colours which may be suitable. Open to other ideas though.
I will provide some of the content, but would like the ability to finish the content myself.
Images and graphics are important. While a few medical photos re great - don't be tempted to us all pictures of doctors and nurses (although a couple would be good) - these are administrative courses so general corporate, eye catching visionary pictures of people in general are great. A medical type picture is also fine.
THE BOOKING system - will be via an ADD ON which will occur at the end of the project and is supplied by a third party software company (our student management system). This project will include up to 2 hours working with the Tech guys from the third party software to enable the ADD ON. If this ADD ON requires more time, we will pay hourly (although I do not expect it will).
Target Market(s)
Mostly a female market, many mature aged women target 25-45 yrs. Mixture of medical/health and corporate. Maybe a bit of mums returning to work and corporate inspiration.
Industry/Entity Type
It Company
Coding
Coded - Design and coding required
Number of Pages Required
5+ page
Requirements
Must have
- Wordpress
- Great graphics
- Interesting
- professional and clean
- Enquiry section (info Pak)
- Should have a University feel to it - Education
- Pages
- Home Page - About Us - Recruitment -Courses - Class Schedule - Traineeships Queensland Funding - Latest News Blog - Corporate Training- Contact us

```html
<!DOCTYPE html>
<html lang="en">
<head>
<meta charset="utf-8">
<title>Harlow Institute of Training</title>
<link rel="stylesheet" href="https://fonts.googleapis.com/css2?family=Cinzel:wght@400;600&family=Lato:wght@400;700&display=swap">
<style>
:root{
  --blue:#1f4e96;
  --blue-dark:#173d78;
  --orange:#f49b36;
  --orange-soft:#f7ab52;
  --ink:#222;
  --muted:#666;
  --light:#efefef;
  --dark:#1b1b1b;
  --darker:#111;
  --white:#fff;
}
*{box-sizing:border-box;margin:0;padding:0}
html,body{width:1200px;height:3403px;overflow:hidden}
body{font-family:'Lato',sans-serif;color:var(--ink);background:var(--white);position:relative;font-size:13px}
.abs{position:absolute}
.serif{font-family:'Cinzel',serif}
.btn{display:inline-block;background:var(--orange);color:var(--white);font-size:12px;font-weight:700;text-align:center;border-radius:2px}

/* header */
.header{position:absolute;left:0;top:0;width:1200px;height:120px;background:var(--white)}
.brand{left:92px;top:6px;width:120px;text-align:center;font-family:'Cinzel',serif;font-weight:600;color:var(--blue);font-size:13px;line-height:15px}
.brand .mark{width:40px;height:40px;border-radius:50%;background:var(--blue);margin:6px auto 0}
.social-tab{left:215px;top:0;width:240px;height:40px;background:#333;border-radius:0 0 18px 18px}
.social-tab span{position:absolute;top:13px;width:14px;height:14px;border-radius:50%;background:#ddd}
.pill{top:7px;height:30px;border-radius:15px;background:var(--white);border:1px solid #ccc;font-size:11px;line-height:28px;color:#555;padding:0 14px}
.search{left:798px;top:7px;width:192px;height:30px;border:1px solid #ccc;border-radius:15px;font-size:11px;line-height:28px;color:#999;padding-left:14px}
.search i{position:absolute;right:3px;top:3px;width:22px;height:22px;border-radius:50%;background:var(--orange)}
.contact{top:55px;font-size:14px;line-height:17px;color:#333;padding-left:38px}
.contact b{color:var(--blue)}
.contact svg{position:absolute;left:0;top:2px}

.nav{position:absolute;left:0;top:120px;width:1200px;height:34px;background:var(--blue)}
.nav ul{list-style:none;display:flex;position:absolute;left:98px;top:0;height:34px}
.nav li{color:var(--white);font-size:11.5px;line-height:34px;padding:0 13px}
.nav li.active{background:var(--orange);font-weight:700;padding:0 20px}

/* hero */
.hero{position:absolute;left:0;top:154px;width:1200px;height:515px;background:linear-gradient(100deg,#5b5b5b 0%,#9a9a9a 40%,#d6d6d6 60%,#7a7a7a 100%)}
.hero-caption{left:91px;top:202px}
.hero-caption h1{display:inline-block;background:rgba(40,40,40,.82);color:var(--white);font-family:'Cinzel',serif;font-weight:400;font-size:30px;padding:8px 10px}
.hero-caption p{background:rgba(40,40,40,.75);color:var(--white);font-size:14px;line-height:20px;width:431px;padding:8px 10px;margin-top:4px}
.dots{left:570px;top:472px;display:flex;gap:8px}
.dots span{width:10px;height:10px;border-radius:50%;background:#fff;opacity:.6}
.dots span:first-child{opacity:1}

/* welcome */
.welcome{position:absolute;left:0;top:669px;width:1200px;height:442px}
.emblem{width:34px;height:34px;border-radius:50%;background:var(--blue)}
h2.title{font-family:'Cinzel',serif;font-weight:400;font-size:28px;color:#111}
h2.title em{font-style:normal;color:var(--blue)}
.welcome-text{left:98px;top:170px;width:680px;font-size:13px;line-height:19.5px;color:#444}
.aside-item{left:840px;width:270px;padding-left:80px}
.aside-item .ico{position:absolute;left:0;top:4px;width:64px;height:64px;border-radius:50%;background:#eee;display:flex;align-items:center;justify-content:center}
.aside-item h3{font-family:'Cinzel',serif;font-weight:400;color:var(--blue);font-size:19px}
.aside-item p{font-size:12.5px;line-height:19px;color:#888}

/* services */
.services{position:absolute;left:0;top:1111px;width:1200px;height:488px;background:var(--light)}
.centered{left:0;width:1200px;text-align:center}
.svc{width:230px;text-align:center}
.svc .ring{width:104px;height:104px;border-radius:50%;border:4px solid var(--orange);background:var(--white);margin:0 auto;display:flex;align-items:center;justify-content:center}
.svc h4{font-family:'Cinzel',serif;font-weight:600;font-size:15px;margin-top:38px;color:#222}
.svc p{font-size:12.5px;line-height:19px;color:#555;margin-top:6px}
.svc .btn{width:102px;height:27px;line-height:27px;margin-top:16px}

/* courses */
.courses{position:absolute;left:0;top:1599px;width:1200px;height:556px}
.course{width:299px;text-align:center}
.course .photo{width:299px;height:188px;box-shadow:0 10px 12px -8px rgba(0,0,0,.5)}
.course h4{font-family:'Cinzel',serif;font-weight:400;font-size:15px;line-height:23px;margin-top:32px;letter-spacing:.5px}
.course .btn{width:112px;height:28px;line-height:28px;margin-top:14px}

/* audience */
.audience{position:absolute;left:0;top:2155px;width:1200px;height:290px;background:linear-gradient(90deg,#141414,#2a2a2a 50%,#141414)}
.aud{width:375px;color:var(--white)}
.aud h3{font-family:'Cinzel',serif;font-weight:400;font-size:29px;padding-left:42px;position:relative}
.aud h3 svg{position:absolute;left:0;top:4px}
.aud p{font-size:12.5px;line-height:20px;margin-top:14px;color:#ddd}
.aud p b{color:var(--white)}
.aud .btn{width:100px;height:30px;line-height:30px;margin-top:16px}
.seal{left:492px;top:27px;width:218px;height:218px;border-radius:50%;background:var(--white);border:6px solid #3a3a3a;display:flex;align-items:center;justify-content:center}
.seal div{width:130px;height:130px;border-radius:50%;background:var(--blue)}

/* promo */
.promo{position:absolute;left:0;top:2445px;width:1200px;height:132px;background:var(--orange-soft)}
.promo p{left:98px;top:36px;width:760px;color:var(--white);font-size:21px;line-height:30px;font-weight:700}
.promo .book{left:980px;top:48px;width:120px;height:36px;line-height:36px;background:#eee;color:#333;font-size:13px;font-weight:700;text-align:center;border:2px solid #ccc}

/* testimonials */
.testimonials{position:absolute;left:0;top:2577px;width:1200px;height:417px}
.quote{width:478px;height:113px;background:#f0f0f0;border-bottom:3px solid var(--orange);padding:18px 20px 0 72px;font-size:13px;line-height:19px;color:#777}
.quote .qm{position:absolute;left:22px;top:14px;font-family:'Cinzel',serif;font-size:44px;color:#ccc;line-height:40px}
.person{display:flex;align-items:center;gap:24px}
.person .avatar{width:58px;height:58px;border-radius:50%;background:linear-gradient(#d9c7b3,#a58c74)}
.person span{font-family:'Cinzel',serif;font-size:13px;letter-spacing:.5px}
.arrow{top:2810px;color:#ccc;font-size:26px}

/* newsletter */
.newsletter{position:absolute;left:0;top:2994px;width:1200px;height:91px;background:var(--dark)}
.newsletter label{left:132px;top:37px;color:#eee;font-size:13px}
.newsletter .field{left:384px;top:31px;width:298px;height:30px;background:var(--darker);border:1px solid #666;color:#ccc;font-size:10px;line-height:28px;padding-left:10px}
.newsletter .sub{left:695px;top:31px;width:95px;height:30px;background:var(--white);color:#111;font-weight:700;font-size:13px;line-height:30px;text-align:center;border-radius:2px}
.newsletter .icons{left:885px;top:40px;display:flex;gap:22px}
.newsletter .icons span{width:12px;height:12px;border-radius:50%;background:#ddd}

.footer{position:absolute;left:0;top:3085px;width:1200px;height:272px;background:var(--darker);color:#ddd}
.footer h5{font-size:16px;font-weight:700;color:var(--white)}
.links{list-style:none;font-size:11px;line-height:16px}
.links li{border-bottom:1px solid #333;padding:8px 0 8px 14px;position:relative}
.links li::before{content:"";position:absolute;left:2px;top:14px;border-left:4px solid #ddd;border-top:3px solid transparent;border-bottom:3px solid transparent}
.info{font-size:11px;line-height:15px;padding-left:18px}
.info svg{position:absolute;left:0;top:2px}
.map{left:645px;top:78px;width:230px;height:140px;background:linear-gradient(135deg,#e8e6df,#d4d8cf)}
.footer-brand{left:940px;top:95px;width:120px;text-align:center;font-family:'Cinzel',serif;font-weight:600;font-size:12px;line-height:15px;color:#ccc}
.footer-brand .mark{width:34px;height:34px;border-radius:50%;background:#ccc;margin:8px auto 0}
.copyright{position:absolute;left:0;top:3357px;width:1200px;height:46px;background:#2a2a2a;color:#ddd;font-size:12px;line-height:46px;text-align:center}
</style>
</head>
<body>

<header class="header">
  <div class="abs brand">Harlow Institute<br>of Training<div class="mark"></div></div>
  <div class="abs social-tab">
    <span style="left:60px"></span><span style="left:95px"></span><span style="left:130px"></span><span style="left:165px"></span><span style="left:200px"></span>
  </div>
  <div class="abs pill" style="left:655px;width:127px">&#9679; Login/Register</div>
  <div class="abs search">Search<i></i></div>
  <div class="abs pill" style="left:1000px;width:102px">English &#9662;</div>
  <div class="abs contact" style="left:692px">
    <svg width="30" height="30" viewBox="0 0 30 30"><path d="M8 3l5 6-3 3c2 4 4 6 8 8l3-3 6 5-4 5C13 27 3 17 4 7z" fill="var(--orange)"/></svg>
    <b>Call Us:</b><br>+61 (7) 5550 2841
  </div>
  <div class="abs contact" style="left:940px">
    <svg width="30" height="24" viewBox="0 0 30 24"><rect x="1" y="2" width="28" height="20" fill="none" stroke="var(--orange)" stroke-width="2.5"/><path d="M1 2l14 11L29 2" fill="none" stroke="var(--orange)" stroke-width="2.5"/></svg>
    <b>Mail Us:</b><br>enquiry@harlowtraining.example
  </div>
</header>

<nav class="nav">
  <ul>
    <li class="active">Home</li><li>About Us</li><li>Recruitment</li><li>Courses</li><li>Class Schedule</li>
    <li>Traineeships Queensland Funding</li><li>Latest News Blog</li><li>Corporate Training</li><li>Contact Us</li>
  </ul>
</nav>

<section class="hero" role="img" aria-label="Photo of a presenter in a suit at a whiteboard in front of a seated business audience">
  <div class="abs hero-caption">
    <h1>Courses for Busy People</h1>
    <p>Our unique FastTrack (Combined Assessment &amp; Training) class format delivers accelerated training that's specifically targeted at busy profes-sionals...</p>
  </div>
  <div class="abs dots"><span></span><span></span><span></span><span></span></div>
</section>

<section class="welcome">
  <div class="abs emblem" style="left:102px;top:40px"></div>
  <h2 class="abs title" style="left:98px;top:92px">Welcome to <em>Harlow Institute of Training</em></h2>
  <div class="abs welcome-text">
    <p>Harlow is Australia's Leading Provider of Educational, Training and Support Services for the Medical and Dental industry -  enabling students to be immediately skilled and 'Job Ready' for a career in Health.</p>
    <p>Harlow is a Registered Training Organisation offering specialised Medical Administration Training in over 15 locations Australia wide.  Harlow have trained thousands of students the required knowledge and skills to become successful health care administrators.</p>
    <p>Our unique Short Medical Reception and Terminology Course and our Full Qualification is Nationally Accredited and the go-to recognised qualification in industry.</p>
  </div>
  <span class="abs btn" style="left:98px;top:374px;width:99px;height:30px;line-height:30px">Read More</span>

  <div class="abs aside-item" style="top:120px">
    <div class="ico"><svg width="34" height="26" viewBox="0 0 34 26"><path d="M17 5C12 1 6 1 1 3v21c5-2 11-2 16 1 5-3 11-3 16-1V3c-5-2-11-2-16 2z" fill="#333"/><path d="M17 5v20" stroke="#eee" stroke-width="1.5"/></svg></div>
    <h3>Story</h3><p>Harlow Health Management started business in February 1999 primarily.. [ » ]</p>
  </div>
  <div class="abs aside-item" style="top:212px">
    <div class="ico"><svg width="36" height="22" viewBox="0 0 36 22"><path d="M1 11C8 1 28 1 35 11 28 21 8 21 1 11z" fill="#333"/><circle cx="18" cy="11" r="6" fill="#eee"/><circle cx="18" cy="11" r="3" fill="#333"/></svg></div>
    <h3>Vision</h3><p>Harlow Health Management started business in February 1999 primarily.. [ » ]</p>
  </div>
  <div class="abs aside-item" style="top:304px">
    <div class="ico"><svg width="36" height="24" viewBox="0 0 36 24"><path d="M2 8l8-6 8 4 8-4 8 6-4 6-10 8-4-3-10-6z" fill="#333"/><path d="M12 9l6 4 6-4" fill="none" stroke="#eee" stroke-width="1.5"/></svg></div>
    <h3>Core Values</h3><p>Harlow Health Management started business in February 1999 primarily.. [ » ]</p>
  </div>
</section>

<section class="services">
  <div class="abs emblem" style="left:583px;top:40px"></div>
  <h2 class="abs title centered" style="top:80px">Our <em>Service</em></h2>

  <div class="abs svc" style="left:103px;top:166px">
    <div class="ring"><svg width="50" height="46" viewBox="0 0 50 46"><rect x="8" y="4" width="38" height="26" fill="none" stroke="#222" stroke-width="3"/><circle cx="8" cy="20" r="5" fill="#222"/><path d="M2 44V30h12v14M14 30l10-8" stroke="#222" stroke-width="4" fill="#222"/><path d="M28 24l6-8 5 4 5-9" fill="none" stroke="#222" stroke-width="2"/></svg></div>
    <h4>Training &amp; Assessment</h4>
    <p>Lorem ipsum dolor sit amet, ectetuer adipiscing elit, sed diam nonummy nibh euismod tincidunt ut laoreet dolore</p>
    <span class="btn">Read More</span>
  </div>
  <div class="abs svc" style="left:355px;top:166px">
    <div class="ring"><svg width="50" height="44" viewBox="0 0 50 44"><rect x="19" y="2" width="12" height="10" fill="#222"/><path d="M25 12v8M7 20h36M7 20v6M25 20v6M43 20v6" stroke="#222" stroke-width="2.5" fill="none"/><rect x="1" y="26" width="12" height="10" fill="#222"/><rect x="19" y="26" width="12" height="10" fill="#222"/><rect x="37" y="26" width="12" height="10" fill="#222"/><rect x="1" y="40" width="48" height="3" fill="#222"/></svg></div>
    <h4>Business &amp; Management</h4>
    <p>Lorem ipsum dolor sit amet, ectetuer adipiscing elit, sed diam nonummy nibh euismod tincidunt ut laoreet dolore</p>
    <span class="btn">Read More</span>
  </div>
  <div class="abs svc" style="left:611px;top:166px">
    <div class="ring"><svg width="46" height="40" viewBox="0 0 46 40"><path d="M5 26a18 18 0 0 1 36 0z" fill="#222"/><rect x="1" y="26" width="44" height="6" rx="2" fill="#222"/><rect x="20" y="6" width="6" height="20" fill="#fff"/></svg></div>
    <h4>Work Health &amp; Safety</h4>
    <p>Lorem ipsum dolor sit amet, ectetuer adipiscing elit, sed diam nonummy nibh euismod tincidunt ut laoreet dolore</p>
    <span class="btn">Read More</span>
  </div>
  <div class="abs svc" style="left:865px;top:166px">
    <div class="ring"><svg width="44" height="50" viewBox="0 0 44 50"><rect x="3" y="5" width="30" height="42" fill="none" stroke="#222" stroke-width="3"/><rect x="12" y="1" width="12" height="8" fill="#222"/><path d="M9 17h18M9 24h18M9 31h12" stroke="#222" stroke-width="2.5"/><circle cx="33" cy="38" r="10" fill="#222"/><path d="M28 38l4 4 6-7" stroke="#fff" stroke-width="2.5" fill="none"/></svg></div>
    <h4>Project Management</h4>
    <p>Lorem ipsum dolor sit amet, ectetuer adipiscing elit, sed diam nonummy nibh euismod tincidunt ut laoreet dolore</p>
    <span class="btn">Read More</span>
  </div>
</section>

<section class="courses">
  <div class="abs emblem" style="left:583px;top:40px"></div>
  <h2 class="abs title centered" style="top:92px">Our <em>Courses</em></h2>

  <div class="abs course" style="left:109px;top:186px">
    <div class="photo" role="img" aria-label="Photo of a receptionist helping a patient at a medical front desk" style="background:linear-gradient(120deg,#d8d3cc,#a89c90 60%,#e2ded8)"></div>
    <h4>Medical Reception<br>&amp; Terminology</h4>
    <span class="btn">Read More</span>
  </div>
  <div class="abs course" style="left:450px;top:186px">
    <div class="photo" role="img" aria-label="Photo of a smiling group of business professionals" style="background:linear-gradient(120deg,#c9d3de,#8193a8 55%,#dfe5ec)"></div>
    <h4>Cert III Business<br>Administration</h4>
    <span class="btn">Read More</span>
  </div>
  <div class="abs course" style="left:792px;top:186px">
    <div class="photo" role="img" aria-label="Photo of a stethoscope and pen resting on paperwork" style="background:linear-gradient(120deg,#e9eef2,#9fb3c2 55%,#f2f4f6)"></div>
    <h4>Medical<br>Terminology</h4>
    <span class="btn">Read More</span>
  </div>
</section>

<section class="audience">
  <div class="abs aud" style="left:91px;top:42px">
    <h3><svg width="30" height="34" viewBox="0 0 30 34"><circle cx="15" cy="8" r="7" fill="#fff"/><path d="M2 34c0-10 5-16 13-16s13 6 13 16z" fill="#fff"/></svg>For the Candidate</h3>
    <p><b>Looking for a Career in Medical Administration?</b><br>Our partner company, Harlow Institute of Training has been the market leader in Medical Reception Training in Australia for over 17 years.  In fact, we pioneered.</p>
    <span class="btn">Read More</span>
  </div>
  <div class="abs seal"><div></div></div>
  <div class="abs aud" style="left:737px;top:42px">
    <h3><svg width="30" height="34" viewBox="0 0 30 34"><circle cx="15" cy="8" r="7" fill="#fff"/><path d="M2 34c0-10 5-16 13-16s13 6 13 16z" fill="#fff"/></svg>For the Employer</h3>
    <p>Harlow Recruitment is a leading National Health Specialist Recruitment Agency with expertise in Medical and Dental administration recruitment for both permanent and temporary staff.</p>
    <span class="btn">Read More</span>
  </div>
</section>

<section class="promo">
  <p class="abs">Enrol In Our BSB51915 Diploma Of Liadership And Managemenr And Gain Vaaluable Skills To Launch Your Management Career.</p>
  <span class="abs book">Booking Now</span>
</section>

<section class="testimonials">
  <div class="abs emblem" style="left:583px;top:40px"></div>
  <h2 class="abs title centered" style="top:92px">Client <em>Testimonials</em></h2>
  <div class="abs quote" style="left:100px;top:172px"><span class="qm">“</span>Siam nonummy nibh euismod tincidunt ut laoreet do magna aliquam erat volutpat. Ut wisi enim ad minim veniam,  v illum dolore eu feugiat nulla facilisis at vero eros et accumsan etl. iusto odio dig.</div>
  <div class="abs quote" style="left:622px;top:172px"><span class="qm">“</span>Siam nonummy nibh euismod tincidunt ut laoreet do magna aliquam erat volutpat. Ut wisi enim ad minim veniam,  v illum dolore eu feugiat nulla facilisis at vero eros et accumsan etl. iusto odio dig.</div>
  <div class="abs person" style="left:130px;top:313px"><div class="avatar" role="img" aria-label="Portrait photo of the client"></div><span>Joan Pell</span></div>
  <div class="abs person" style="left:652px;top:313px"><div class="avatar" role="img" aria-label="Portrait photo of the client" style="background:linear-gradient(#b9a898,#6f5f52)"></div><span>Owen Brask</span></div>
</section>
<span class="abs arrow" style="left:72px">‹</span>
<span class="abs arrow" style="left:1116px">›</span>

<section class="newsletter">
  <label class="abs">Stay updated with latest news from</label>
  <div class="abs field">Enter Your Email</div>
  <div class="abs sub">Subscribe</div>
  <div class="abs icons"><span></span><span></span><span></span><span></span><span></span></div>
</section>

<footer class="footer">
  <h5 class="abs" style="left:102px;top:22px">Quick Link</h5>
  <ul class="abs links" style="left:102px;top:58px;width:110px">
    <li>Home</li><li>About Us</li><li>Courses</li><li>Recruitment</li><li>Class Schedule</li>
  </ul>
  <ul class="abs links" style="left:215px;top:58px;width:130px">
    <li>Latest News Blog</li><li>Corporate Training</li><li>Contact Us</li>
  </ul>
  <ul class="abs links" style="left:102px;top:232px;width:245px"><li style="border:none">Traineeships Queensland Funding</li></ul>

  <h5 class="abs" style="left:383px;top:22px">Information</h5>
  <div class="abs info" style="left:383px;top:70px">
    <svg width="10" height="14" viewBox="0 0 10 14"><path d="M5 0a5 5 0 0 1 5 5c0 4-5 9-5 9S0 9 0 5a5 5 0 0 1 5-5z" fill="#ddd"/><circle cx="5" cy="5" r="2" fill="#111"/></svg>
    Harlow Health Trainings<br>123, Ut wisi enim ad minim ve,<br>Mor nostrui tation -123 456
  </div>
  <div class="abs info" style="left:383px;top:140px">
    <svg width="11" height="11" viewBox="0 0 30 30"><path d="M8 3l5 6-3 3c2 4 4 6 8 8l3-3 6 5-4 5C13 27 3 17 4 7z" fill="#ddd"/></svg>
    +61 (7) 5550 2841
  </div>
  <div class="abs info" style="left:383px;top:172px">
    <svg width="12" height="10" viewBox="0 0 30 24"><rect x="1" y="2" width="28" height="20" fill="#ddd"/><path d="M1 2l14 11L29 2" fill="none" stroke="#111" stroke-width="3"/></svg>
    info@harlowtraining.example
  </div>

  <h5 class="abs" style="left:645px;top:22px">Location Map</h5>
  <div class="abs map" role="img" aria-label="Street map with a pin marking 14 Bramble St"></div>

  <div class="abs footer-brand">Harlow Institute<br>of Training<div class="mark"></div></div>
</footer>
<div class="copyright">© 2016 Harlow Health Trainings. All Right Reserved</div>

</body>
</html>
```